Remodeling brochure

We need an informative homeowner friendly brochure detailing our company and things we do. We are looking for an initial setup and ideas (# of pages, etc) and then we will send more content. We are uploading our logo design. We are a high end remodeling company specializing in kitchen & bath remodels. We sell ourselves on customer communication and attention to detail in our designs and remodels.

Target Market(s)

Residential homeowners

Contact Information for Business Card

Modern and attention grabbing

Requirements
Must have
• Name- Hearth & Tile Works<br/>Address- 718 NW Larkfield Drive Suite #207<br/> Ankeny, Iowa 50099<br/>Phone- 515-555-0184<br/>email-htworksiowa@example-mail.com

```html
<!DOCTYPE html>
<html lang="en">
<head>
<meta charset="utf-8">
<title>Hearth &amp; Tile Works – Brochure Pages</title>
<link href="https://fonts.googleapis.com/css2?family=Anton&family=Montserrat:ital,wght@0,400;0,500;0,600;0,700;1,700&display=swap" rel="stylesheet">
<style>
:root{
  --stage:#a3a3a3;
  --blue:#2a8bd1;
  --deep-blue:#3d5fae;
  --ink:#262626;
  --charcoal:#2c2c2c;
  --white:#ffffff;
  --photo-kitchen:linear-gradient(160deg,#d9d6cf 0%,#b9b4a8 45%,#8a7a66 100%);
  --photo-dark-kitchen:linear-gradient(160deg,#f0f0ee 0%,#9a9b9c 55%,#4a4c50 100%);
  --photo-bath:linear-gradient(150deg,#f2f2f0 0%,#d8d8d6 45%,#55585e 100%);
  --photo-open-kitchen:linear-gradient(160deg,#f4f3f0 0%,#cfc9c0 50%,#8d6e55 100%);
}
*{margin:0;padding:0;box-sizing:border-box}
html,body{width:1200px;height:3550px;overflow:hidden}
body{background:var(--stage);position:relative;font-family:"Montserrat",sans-serif;color:var(--ink)}
.abs{position:absolute}
.anton{font-family:"Anton",sans-serif;font-weight:400}
.page{position:absolute;background:var(--white)}
.photo{position:absolute}
.para{position:absolute;font-size:10.5px;line-height:15px;font-weight:500;color:var(--ink)}
.vertical{position:absolute;transform-origin:0 0;transform:rotate(-90deg);white-space:nowrap;line-height:1}

/* cover */
.cover-header{left:298px;top:91px;width:603px;height:128px;background:var(--charcoal)}
.brand{position:absolute;left:490px;top:140px;display:flex;align-items:center;gap:10px;font-size:18px;font-weight:600;color:var(--blue);letter-spacing:1px}
.brand-square{width:28px;height:28px;background:var(--blue)}
.cover-tag{left:359px;font-size:17px;line-height:20px;font-weight:500;white-space:nowrap}
.cover-title{left:358px;top:846px;font-size:50px;line-height:1;letter-spacing:-0.5px;color:var(--ink);white-space:nowrap}
.cover-year{left:722px;top:830px;font-size:34px;line-height:1.2;letter-spacing:7px;color:var(--ink)}

/* contents */
.toc-num{right:810px;font-size:31px;color:var(--white);text-align:right}
.toc-title{right:805px;font-size:19px;font-weight:500;color:var(--white);text-align:right;white-space:nowrap}

/* rule with accent */
.rule{position:absolute;height:1px}
.rule-accent{position:absolute;height:3px}
.small-label{position:absolute;font-size:11px;font-weight:700}
.blue-head{position:absolute;color:var(--blue);line-height:1}
.side-para{font-size:10px;line-height:15px}
</style>
</head>
<body>

<!-- Cover -->
<section class="page" style="left:267px;top:80px;width:634px;height:887px"></section>
<div class="abs cover-header"></div>
<div class="brand"><span class="brand-square"></span><span>Hearth &amp; Tile Works</span></div>
<div class="photo" role="img" aria-label="Bright traditional kitchen with cream cabinets, range hood and wood floor" style="left:303px;top:220px;width:595px;height:560px;background:var(--photo-kitchen)"></div>
<div class="abs" style="left:277px;top:452px;width:25px;height:329px;background:var(--blue)"></div>
<div class="abs cover-tag" style="top:822px">specializing in</div>
<div class="abs anton cover-title">Kitchen &amp; bath</div>
<div class="abs cover-tag" style="top:893px">remodels</div>
<div class="abs anton cover-year">2020</div>
<div class="abs" style="left:714px;top:894px;width:117px;height:62px;background:var(--blue)"></div>

<!-- Contents spread -->
<section class="page" style="left:88px;top:1053px;width:1006px;height:704px"></section>
<div class="abs" style="left:95px;top:1060px;width:576px;height:690px;background:var(--blue)"></div>
<div class="abs" style="left:440px;top:1271px;width:231px;height:423px;background:var(--white)"></div>
<div class="photo" role="img" aria-label="Modern kitchen with charcoal cabinets and white countertops" style="left:671px;top:1060px;width:346px;height:209px;background:var(--photo-dark-kitchen)"></div>
<div class="abs" style="left:1029px;top:1060px;width:58px;height:209px;background:var(--blue)"></div>

<div class="abs anton toc-num" style="top:1186px">01</div>
<div class="abs toc-title" style="top:1240px">Title Goes Here</div>
<div class="abs anton toc-num" style="top:1288px">02</div>
<div class="abs toc-title" style="top:1346px">Another Title Here</div>
<div class="abs anton toc-num" style="top:1397px">03</div>
<div class="abs toc-title" style="top:1452px">Page Headline Here</div>
<div class="abs anton toc-num" style="top:1498px">04</div>
<div class="abs toc-title" style="top:1558px">Headline Here</div>
<div class="abs anton toc-num" style="top:1608px">05</div>
<div class="abs toc-title" style="top:1664px">Another Headline</div>

<div class="vertical anton" style="left:470px;top:1614px;font-size:84px;color:var(--ink)">CONTENT</div>

<div class="abs" style="left:671px;top:1316px;font-size:20px;font-weight:500">Welcome To</div>
<div class="abs anton" style="left:671px;top:1346px;font-size:52px;line-height:1.1">COMPANY</div>
<div class="abs" style="left:745px;top:1437px;width:7px;height:40px;background:var(--ink)"></div>
<p class="para" style="left:774px;top:1436px;width:250px">Lorem ipsum dolor sit amet, consectetur adipiscing elit. Sed molestie luctus est, quis malesuada purus volutpat nec. Sed fermentum tellus rhoncus lacus venenatis pellentesque. Vivamus nisl augue, lacinia sit amet augue sit amet, scelerisque porta elit. Aliquam erat volutpat.</p>
<p class="para" style="left:774px;top:1572px;width:250px">Donec pretium, tortor et laoreet cursus, magna magna interdum nulla, in aliquet tellus orci sit amet justo. Nullam justo nisi, semper ut lacinia at, tristique at purus. Quisque rhoncus odio a egestas vestibulum.</p>

<!-- Vision spread -->
<section class="page" style="left:88px;top:1896px;width:1006px;height:704px"></section>
<div class="photo" role="img" aria-label="White bathroom with double vanity, dark cabinets, round mirrors and freestanding tub" style="left:88px;top:1954px;width:540px;height:594px;background:var(--photo-bath)"></div>
<div class="rule" style="left:648px;top:1940px;width:323px;background:var(--blue)"></div>
<div class="rule-accent" style="left:869px;top:1939px;width:102px;background:var(--blue)"></div>
<div class="small-label" style="left:989px;top:1934px;color:var(--ink)">Your Logo</div>
<div class="small-label" style="left:648px;top:1954px;color:var(--blue);font-size:9px">Pages 05</div>
<div class="photo" role="img" aria-label="Bathroom vanity with window and mirror" style="left:668px;top:2101px;width:155px;height:148px;background:var(--photo-bath)"></div>
<div class="blue-head anton" style="left:847px;top:2102px;font-size:19px">CONVALLIS JUSTOO</div>
<div class="abs" style="left:847px;top:2135px;font-size:11px;font-weight:700;font-style:italic">Magna Lobortisr</div>
<p class="para side-para" style="left:847px;top:2158px;width:205px">Integer sed eleifend massa. Suspendisse hendrerit purus ac magna lobortis, sit amet convallis justo sagittis. Sed non dui libero. Quisque et sagittis ex, et dapibus mi. Maecenas eu faucibus leo.</p>
<div class="rule" style="left:668px;top:2272px;width:377px;background:var(--blue)"></div>
<div class="blue-head anton" style="left:668px;top:2296px;font-size:27px;line-height:39px">Our Vision ,<br>Mission And<br>Value</div>
<p class="para side-para" style="left:847px;top:2296px;width:205px">Phasellus ut accumsan purus. Nam male suada lorem a velit pretium pellentesque eget eget magna. Aenean non massa lacinia, laoreet lacus nec, placerat velit. Proin tincidunt, magna et fermentum posuere, turpis velit pulvinar odio, volu tpat pulvinar velit lorem sed ex.</p>
<p class="para side-para" style="left:847px;top:2418px;width:205px">Proin dictum arcu eu felis efficitur, ut iaculis risus accumsan. Donec odio arcu tempor eu imperdiet facilisis, pretium eget velit. Ut egestas nulla nibh, nec consectetur risus sagittis sit amet. Sed maximus, arcu nec porttitor mattiseget elit. Donec nec nisi arcu.</p>

<!-- Quote spread -->
<section class="page" style="left:88px;top:2757px;width:1006px;height:704px"></section>
<div class="abs" style="left:95px;top:2764px;width:992px;height:690px;background:var(--blue)"></div>
<div class="rule" style="left:135px;top:2804px;width:324px;background:var(--white)"></div>
<div class="rule-accent" style="left:357px;top:2803px;width:102px;background:var(--white)"></div>
<div class="small-label" style="left:477px;top:2798px;color:var(--white)">Your Logo</div>
<div class="small-label" style="left:135px;top:2818px;color:var(--white);font-size:9px">Pages 06</div>
<div class="rule" style="left:638px;top:2802px;width:324px;background:var(--white)"></div>
<div class="rule-accent" style="left:860px;top:2801px;width:102px;background:var(--white)"></div>
<div class="small-label" style="left:989px;top:2796px;color:var(--white)">Your Logo</div>
<div class="small-label" style="left:638px;top:2816px;color:var(--white);font-size:9px">Pages 07</div>

<div class="abs" style="left:219px;top:2884px;width:3px;height:517px;background:var(--white)"></div>
<p class="para" style="left:241px;top:2956px;width:132px;color:var(--white);font-size:10px;line-height:15.2px">Lorem ipsum dolor sit amet, consectetuer adipiscing elit, sed diam nonummy nibh euismod tincidunt ut laoreet dolore magna aliquam erat volutpat. Ut wisi enim ad minim veniam, quis nostrud exerci tation ullamcorper su scipit lobortis nisl ut aliquip ex ea commodo consequat. Duis autem vel eum iriure dolor in hendrerit in vulputate velit esse molestie co nsequat, vel illum dolore eu feugiat nulla facilisis at vero eros et accumsan et iusto odio dignissim qui blandit praesent luptatum zzril</p>
<div class="vertical anton" style="left:172px;top:3406px;font-size:37px;color:var(--white)">HEADLINE HERE</div>
<div class="vertical" style="left:140px;top:3406px;font-size:19px;color:var(--white)">Subtitle</div>

<div class="photo" role="img" aria-label="Bright white kitchen with open wood shelves, range hood and marble island" style="left:395px;top:2890px;width:395px;height:537px;background:var(--photo-open-kitchen)"></div>
<div class="abs" style="left:790px;top:2890px;width:297px;height:537px;background:var(--deep-blue)"></div>
<svg class="abs" style="left:780px;top:2858px" width="60" height="56" viewBox="0 0 60 56" aria-hidden="true">
  <path fill="#fff" d="M4 56V30C4 14 11 4 26 0v10c-7 3-10 8-10 16h10v30z"/>
  <path fill="#fff" d="M34 56V30C34 14 41 4 56 0v10c-7 3-10 8-10 16h10v30z"/>
</svg>
<blockquote class="abs" style="left:838px;top:2970px;width:240px;font-size:30px;line-height:39.3px;color:var(--white);letter-spacing:0.5px">Success isn’t<br>just about<br>what you ac-<br>complish in<br>your life; it’s<br>about what<br>you inspire<br>others to do.</blockquote>

</body>
</html>
```